Business Card - connecting 2 souls and beggining the journey of self discovery

Logo on the front
with tag line

On the back list of services and contact details

Seminars
workshops
Coaching
podcasts

Darren Whitlow
Health & Wellbeing Life Coach
0491 372 615
darren@brightcoreliving.example
brightcoreliving.example

Industry/Entity Type

Life Coaching

Contact Information for Business Card

I like the use of colour from the logo to be used. I'm not a fan of white.

Requirements
Must have
• My tagline: The journey home starts with you
Nice to have
• Use of colour that is in the Brightcore Living logo

```html
<!DOCTYPE html>
<html lang="en">
<head>
<meta charset="utf-8">
<title>Brightcore Living – Business Card</title>
<link href="https://fonts.googleapis.com/css2?family=Quicksand:wght@500;700&display=swap" rel="stylesheet">
<style>
  :root {
    --bg: #ecebef;
    --card: #f7f0fa;
    --card-warm: #fdf3ea;
    --purple: #55267f;
    --purple-ink: #4a2370;
    --grey-ink: #5a5560;
    --red: #e8413c;
    --orange: #f7a21b;
    --yellow: #f3d21b;
    --green: #7cc242;
    --violet: #8a3fa0;
  }
  * { box-sizing: border-box; margin: 0; padding: 0; }
  html, body { width: 1200px; height: 801px; overflow: hidden; }
  body {
    background: var(--bg);
    font-family: "Quicksand", sans-serif;
    position: relative;
  }
  .card {
    position: absolute;
    top: 245px;
    width: 540px;
    height: 310px;
    background: linear-gradient(120deg, var(--card) 0%, var(--card-warm) 100%);
    border-radius: 24px;
    overflow: hidden;
    box-shadow: 0 10px 30px rgba(40, 20, 60, 0.15);
  }
  .card--front { left: 40px; }
  .card--back { left: 620px; }

  /* front */
  .front-halo {
    position: absolute;
    left: -40px;
    top: 10px;
    width: 290px;
    height: 290px;
    border-radius: 50%;
    background: linear-gradient(135deg, #f4c6d6 0%, #fbe6b8 45%, #d8efc4 75%, #c9e7ee 100%);
    opacity: 0.9;
  }
  .brand {
    position: absolute;
    display: flex;
    flex-direction: column;
    align-items: center;
    text-align: center;
  }
  .brand__dot {
    border-radius: 50%;
    background: linear-gradient(135deg, var(--red), var(--orange) 40%, var(--yellow) 55%, var(--green) 80%, var(--violet));
  }
  .brand__name {
    color: var(--purple-ink);
    font-weight: 700;
    letter-spacing: 0.02em;
    white-space: nowrap;
  }
  .brand__tagline {
    color: var(--purple-ink);
    font-weight: 700;
    white-space: nowrap;
  }
  .card--front .brand { left: 272px; top: 70px; width: 256px; }
  .card--front .brand__dot { width: 92px; height: 92px; margin-bottom: 14px; }
  .card--front .brand__name { font-size: 22px; }
  .card--front .brand__tagline { font-size: 15px; margin-top: 6px; }

  /* back */
  .card--back .brand { left: 18px; top: 26px; width: 236px; }
  .card--back .brand__dot { width: 78px; height: 78px; margin-bottom: 10px; }
  .card--back .brand__name { font-size: 18px; }
  .card--back .brand__tagline { font-size: 13px; margin-top: 4px; }

  .person {
    position: absolute;
    right: 26px;
    top: 40px;
    text-align right;
    text-align: right;
  }
  .person__name {
    color: var(--purple-ink);
    font-weight: 700;
    font-size: 26px;
    letter-spacing: 0.01em;
    white-space: nowrap;
  }
  .person__title {
    color: var(--grey-ink);
    font-weight: 500;
    font-size: 14px;
    margin-top: 2px;
  }
  .info-band {
    position: absolute;
    left: 0;
    right: 0;
    bottom: 0;
    height: 142px;
    background: var(--purple);
    color: #fff;
    display: flex;
    justify-content: space-between;
    padding: 22px 26px 0 26px;
  }
  .contact-list { list-style: none; }
  .contact-list li {
    display: flex;
    align-items: center;
    gap: 12px;
    font-size: 14px;
    font-weight: 700;
    height: 32px;
    white-space: nowrap;
  }
  .contact-list svg { width: 24px; height: 24px; flex: none; }
  .services {
    display: grid;
    grid-template-columns: auto auto;
    column-gap: 24px;
    row-gap: 8px;
    list-style: none;
    align-content: start;
    padding-top: 4px;
  }
  .services li {
    font-size: 15px;
    font-weight: 700;
    display: flex;
    align-items: center;
    gap: 7px;
  }
  .services li::before {
    content: "";
    width: 6px;
    height: 6px;
    border-radius: 50%;
    background: #fff;
  }
</style>
</head>
<body>

  <section class="card card--front" aria-label="Card front">
    <div class="front-halo"></div>
    <div class="brand">
      <div class="brand__dot"></div>
      <div class="brand__name">Brightcore Living</div>
      <div class="brand__tagline">The journey home starts with you</div>
    </div>
  </section>

  <section class="card card--back" aria-label="Card back">
    <div class="brand">
      <div class="brand__dot"></div>
      <div class="brand__name">Brightcore Living</div>
      <div class="brand__tagline">The journey home starts with you</div>
    </div>

    <div class="person">
      <div class="person__name">Darren Whitlow</div>
      <div class="person__title">Health &amp; Wellbeing Life Coach</div>
    </div>

    <div class="info-band">
      <ul class="contact-list">
        <li>
          <svg viewBox="0 0 24 24" aria-hidden="true">
            <circle cx="12" cy="12" r="12" fill="#fff"/>
            <path d="M8.2 6.5l2 2.2-1.1 1.6c.8 1.7 2 2.9 3.7 3.7l1.6-1.1 2.2 2-1 1.7c-3.8-.3-7.8-4.3-8.1-8.1z" fill="#55267f"/>
          </svg>
          0491 372 615
        </li>
        <li>
          <svg viewBox="0 0 24 24" aria-hidden="true">
            <circle cx="12" cy="12" r="12" fill="#fff"/>
            <rect x="6" y="8" width="12" height="8.5" rx="1" fill="none" stroke="#55267f" stroke-width="1.5"/>
            <polyline points="6.5,8.7 12,13 17.5,8.7" fill="none" stroke="#55267f" stroke-width="1.5"/>
          </svg>
          darren@brightcoreliving.example
        </li>
        <li>
          <svg viewBox="0 0 24 24" aria-hidden="true">
            <circle cx="12" cy="12" r="12" fill="#fff"/>
            <circle cx="12" cy="12" r="6.5" fill="none" stroke="#55267f" stroke-width="1.5"/>
            <ellipse cx="12" cy="12" rx="2.8" ry="6.5" fill="none" stroke="#55267f" stroke-width="1.3"/>
            <line x1="5.5" y1="12" x2="18.5" y2="12" stroke="#55267f" stroke-width="1.3"/>
          </svg>
          www.brightcoreliving.example
        </li>
      </ul>
      <ul class="services">
        <li>Seminars</li>
        <li>Coaching</li>
        <li>Workshops</li>
        <li>Podcasts</li>
      </ul>
    </div>
  </section>

</body>
</html>
```